Business Card Design needed for start up company Halvora

In need of a new business card designed for a start up company based in Sydney, Halvora is a new start up innovative Company, our mission it to make property accessible for everyday Australian and to become the leading Real Estate platform in Australia. We want it to be fresh and clean.

Industry/Entity Type

Financial

Contact Information for Business Card

Section for Name
Section for Title

HALVORA - The Strength of Pooling
Mobile:
Direct:

Font styles to use
Sans Serif

Colors
33a6d7
0692cd
0255a3
ffffff

Requirements
Must have
• Logo, all business card details

```html
<!DOCTYPE html>
<html lang="en">
<head>
<meta charset="utf-8">
<title>Halvora Business Card</title>
<link href="https://fonts.googleapis.com/css2?family=Roboto:wght@400;500;700;900&display=swap" rel="stylesheet">
<style>
  :root {
    --navy: #1f3f78;
    --blue-deep: #0255a3;
    --blue-mid: #0692cd;
    --blue-light: #33a6d7;
    --white: #ffffff;
    --paper: #f6f6f6;
    --ink: #3d4650;
    --backdrop: #2b2b2b;
  }
  * { margin: 0; padding: 0; box-sizing: border-box; }
  html, body { width: 1200px; height: 886px; overflow: hidden; }
  body {
    background: var(--backdrop);
    font-family: "Roboto", Arial, sans-serif;
    display: flex;
    flex-direction: column;
    align-items: center;
    justify-content: center;
    gap: 60px;
  }
  .card {
    width: 620px;
    height: 354px;
    border-radius: 22px;
    position: relative;
    overflow: hidden;
  }
  .brand {
    display: flex;
    align-items: center;
    gap: 12px;
  }
  .brand-dot {
    border-radius: 50%;
    background: var(--blue-light);
    flex: none;
  }
  .brand-name {
    font-weight: 900;
    letter-spacing: 1px;
    line-height: 1;
  }

  /* Front */
  .card-front {
    background: var(--navy);
    display: flex;
    flex-direction: column;
    align-items: center;
    justify-content: center;
  }
  .card-front .brand-dot { width: 70px; height: 70px; }
  .card-front .brand-name { font-size: 66px; color: var(--white); }
  .tagline {
    margin-top: 36px;
    color: var(--white);
    font-size: 17px;
    letter-spacing: 0.5px;
  }

  /* Back */
  .card-back { background: var(--paper); }
  .accent-band {
    position: absolute;
    left: 0; top: 34px;
    width: 110px; height: 48px;
    background: var(--blue-deep);
    opacity: 0.85;
  }
  .card-back .brand {
    position: absolute;
    left: 92px; top: 26px;
  }
  .card-back .brand-dot {
    width: 64px; height: 64px;
    border: 4px solid var(--white);
  }
  .card-back .brand-name { font-size: 52px; color: var(--blue-deep); }
  .person {
    position: absolute;
    left: 48px; top: 130px;
  }
  .person-name {
    font-size: 22px; font-weight: 700; color: var(--blue-deep);
  }
  .person-title {
    font-size: 16px; font-weight: 500; color: var(--blue-light); margin-top: 2px;
  }
  .contacts {
    position: absolute;
    left: 48px; top: 198px;
    list-style: none;
  }
  .contacts li {
    display: flex; align-items: center; gap: 10px;
    font-size: 15px; color: var(--ink); line-height: 22px;
  }
  .contacts svg { width: 13px; height: 13px; fill: var(--blue-deep); flex: none; }
  .divider {
    position: absolute;
    left: 258px; top: 250px;
    width: 1.5px; height: 40px;
    background: var(--ink);
  }
  .address {
    position: absolute;
    left: 278px; top: 250px;
    font-size: 15px; color: var(--ink); line-height: 21px;
    font-style: normal;
  }
</style>
</head>
<body>
  <section class="card card-front">
    <div class="brand">
      <span class="brand-dot"></span>
      <span class="brand-name">HALVORA</span>
    </div>
    <p class="tagline">The Strength of Pooling</p>
  </section>

  <section class="card card-back">
    <div class="accent-band"></div>
    <div class="brand">
      <span class="brand-dot"></span>
      <span class="brand-name">HALVORA</span>
    </div>
    <div class="person">
      <p class="person-name">MAREN HOLT</p>
      <p class="person-title">CEO/FOUNDER</p>
    </div>
    <ul class="contacts">
      <li><svg viewBox="0 0 16 16"><path d="M3 1l3 3-2 2c1 2 4 5 6 6l2-2 3 3-2 2C7 15 1 9 1 3z"/></svg>612 481 7730</li>
      <li><svg viewBox="0 0 16 16"><path d="M4 0h8a1 1 0 011 1v14a1 1 0 01-1 1H4a1 1 0 01-1-1V1a1 1 0 011-1zm1 2v10h6V2z"/></svg>614 205 3398</li>
      <li><svg viewBox="0 0 16 16"><path d="M0 3h16v10H0zm1 1v1l7 4 7-4V4z"/></svg>hello@halvora.au</li>
      <li><svg viewBox="0 0 16 16"><circle cx="8" cy="8" r="7"/></svg>www.halvora.au</li>
    </ul>
    <div class="divider"></div>
    <address class="address">42 Wattle Street<br>Sydney, NSW 2000</address>
  </section>
</body>
</html>
```